Bookcover: Ways to Turn Into a Bold Pathfinder

I am publishing a super-low-cost innovation book for €4,99 on Quillmere Open Press to help everyone become a great innovator: young ambitious people without college education nor a big budget. Do you want to help me?

Brief:
Design a book cover 1600 x 2560 pixels for QOP.
Main title: Ways to Turn Into a Bold Pathfinder
Sub title: mindset - insights - skills & tools
Author: Joost ter Brakel
Design: captive, and appealing to everyone
Target Group: young ambitious people without college education

For quillmere please format the height/width ratio of 1.6:1

```html
<!DOCTYPE html>
<html lang="en">
<head>
<meta charset="utf-8">
<title>Ways to Turn Into a Bold Pathfinder — Joost ter Brakel</title>
<link rel="stylesheet" href="https://fonts.googleapis.com/css2?family=Montserrat:wght@300;700;800&display=swap">
<style>
  :root {
    --sky-top: #b7bfd2;
    --sky-mid: #979aa6;
    --floor-light: #c9c9cf;
    --floor-deep: #7c7882;
    --ink-white: #ffffff;
    --burst-core: #ffd24a;
    --burst-warm: #f0742a;
    --burst-pink: #e0386a;
    --burst-cyan: #3cb8d8;
  }
  * { margin: 0; padding: 0; box-sizing: border-box; }
  html, body { width: 750px; height: 1200px; overflow: hidden; }
  body { font-family: 'Montserrat', sans-serif; }

  .cover {
    position: relative;
    width: 750px;
    height: 1200px;
    overflow: hidden;
    background:
      radial-gradient(ellipse 70% 40% at 90% 0%, rgba(210,218,236,0.7), transparent 70%),
      linear-gradient(180deg, var(--sky-top) 0%, var(--sky-mid) 38%, #8f8f98 66%, var(--floor-light) 72%, #a4a2aa 80%, var(--floor-deep) 100%);
    color: var(--ink-white);
    text-align: center;
  }

  .series-line {
    position: absolute;
    top: 36px;
    left: 0; right: 0;
    font-weight: 300;
    font-size: 25px;
    letter-spacing: 0.5px;
  }

  .author {
    position: absolute;
    top: 74px;
    left: 0; right: 0;
    font-weight: 800;
    font-size: 50px;
    letter-spacing: 2px;
  }

  .hero-art {
    position: absolute;
    top: 180px;
    left: 0;
    width: 750px;
    height: 770px;
    background:
      radial-gradient(ellipse 16% 20% at 50% 48%, #fff4c2 0%, var(--burst-core) 45%, transparent 100%),
      radial-gradient(ellipse 30% 32% at 50% 46%, var(--burst-warm) 0%, rgba(240,116,42,0.6) 55%, transparent 100%),
      radial-gradient(ellipse 45% 40% at 35% 40%, rgba(60,184,216,0.55) 0%, transparent 70%),
      radial-gradient(ellipse 45% 40% at 68% 42%, rgba(224,56,106,0.5) 0%, transparent 70%),
      radial-gradient(ellipse 60% 48% at 50% 45%, rgba(255,170,60,0.45) 0%, transparent 80%);
  }

  .title {
    position: absolute;
    top: 962px;
    left: 0; right: 0;
    font-weight: 800;
    line-height: 1;
  }
  .title-lead {
    display: block;
    font-size: 25px;
    letter-spacing: 3px;
    margin-left: 20px;
  }
  .title-main {
    display: block;
    font-size: 80px;
    letter-spacing: 0;
    margin-top: 20px;
    margin-left: 20px;
  }
  .title-hero {
    display: block;
    font-size: 74px;
    margin-top: 10px;
    margin-left: 10px;
  }
</style>
</head>
<body>
  <main class="cover">
    <p class="series-line">MINDSET - INSIGHTS - SKILLS &amp; TOOLS</p>
    <p class="author">JOOST TER BRAKEL</p>

    <div class="hero-art" role="img" aria-label="A glowing light bulb bursting into a colourful explosion of paint splashes in orange, yellow, cyan and pink on a grey surface"></div>

    <h1 class="title">
      <span class="title-lead">WAYS TO TURN INTO A</span>
      <span class="title-main">BOLD</span>
      <span class="title-hero">PATHFINDER</span>
    </h1>
  </main>
</body>
</html>
```